LEARN Business Skills so you can Earn a good living

size of the poster is 8”x 10.75" plus 0.25" bleed.
Please leave 1 inch on the bottoum for footer
I want a design a poster that will attract people's attention.
I appreciate a creative ad however the ad should not take away from being able to clearly read the text.
-I also appreciate a simple creative ad that is not too busy.
-you can use graphics, vectors, or pictures of real people.
-however, if you use real people it should be a white male that is wearing a white shirt and look like a professional person.

Target Market(s)

Potential young business people

Industry/Entity Type

education

Requirements
Must have
• easy to read the text
Nice to have
• I would like a "creative" simple ad that is easy to be read
Should not have
• pictures of women

```html
<!DOCTYPE html>
<html lang="en">
<head>
<meta charset="utf-8">
<title>Learn to Earn – Business Enrichment Course</title>
<link rel="stylesheet" href="https://fonts.googleapis.com/css2?family=Poppins:wght@400;600;700;800&display=swap">
<style>
  :root {
    --cream: #f5e1cb;
    --sand: #f6d195;
    --white: #ffffff;
    --brown: #722a1c;
    --orange: #f28a22;
    --ink: #1d1d1d;
    --art-a: #e9d3bd;
    --art-b: #7aa9d8;
  }
  * { margin: 0; padding: 0; box-sizing: border-box; }
  html, body { width: 921px; height: 1200px; overflow: hidden; background: var(--white); }
  .poster {
    position: relative;
    width: 921px;
    height: 1200px;
    background: var(--cream);
    font-family: 'Poppins', sans-serif;
    color: var(--ink);
    overflow: hidden;
  }
  .backdrop { position: absolute; inset: 0; }
  .headline {
    position: absolute; left: 0; width: 100%; top: 120px;
    text-align: center; font-weight: 800; font-size: 89px; line-height: 1;
    color: var(--brown); letter-spacing: -1px; white-space: nowrap;
  }
  .course-title {
    position: absolute; left: 0; width: 100%; top: 212px;
    text-align: center; font-weight: 800; font-size: 44.5px; line-height: 1;
    color: var(--orange); letter-spacing: -0.5px; white-space: nowrap;
  }
  .tagline {
    position: absolute; left: 0; width: 100%; top: 270px;
    text-align: center; font-weight: 700; font-size: 22px; line-height: 1;
    color: var(--ink); letter-spacing: -0.3px; white-space: nowrap;
  }
  .skills-pill {
    position: absolute; left: 96px; top: 319px; width: 729px; height: 51px;
    border: 2.5px solid var(--brown); border-radius: 26px;
    display: flex; align-items: center; justify-content: center;
    font-weight: 800; font-size: 36px; color: var(--brown); letter-spacing: -0.4px;
    white-space: nowrap;
  }
  .skills-pill .accent { color: var(--orange); margin-left: 10px; }
  .benefit-icon {
    position: absolute; top: 430px; width: 84px; height: 73px;
    background: var(--white); border-radius: 14px;
    display: flex; align-items: center; justify-content: center;
  }
  .benefit-icon svg { width: 44px; height: 44px; }
  .benefit-label {
    position: absolute; top: 443px;
    font-weight: 700; font-size: 19px; line-height: 23px; color: var(--ink);
    white-space: nowrap;
  }
  .lesson-art {
    position: absolute; left: 146px; top: 577px; width: 630px; height: 400px;
    border-radius: 24px 24px 30px 30px;
    background: linear-gradient(160deg, var(--art-b) 0%, var(--art-a) 45%, #3e4a4a 100%);
    opacity: 0.85;
  }
  .topics {
    position: absolute; left: 0; width: 100%; top: 1034px;
    text-align: center; font-weight: 400; font-size: 16px; line-height: 19px;
    color: var(--ink);
  }
  .topics p { white-space: nowrap; }
</style>
</head>
<body>
<main class="poster">
  <svg class="backdrop" viewBox="0 0 921 1200" preserveAspectRatio="none" aria-hidden="true">
    <path fill="#ffffff" d="M0 0 H921 V130 C905 140 895 120 893 100 C870 118 840 120 810 112 C770 140 720 150 670 132 C640 140 610 128 590 112 C560 135 520 138 495 118 C470 140 420 142 395 115 C370 140 320 138 300 110 C275 90 245 55 240 40 C225 50 215 62 205 58 C190 90 160 120 130 126 C95 140 60 130 40 105 C20 90 5 80 0 70 Z"/>
    <path fill="var(--sand)" d="M0 1060 C20 980 120 905 300 885 L700 790 C750 690 820 645 870 648 C900 651 921 668 921 684 V1200 H0 Z"/>
  </svg>

  <h1 class="headline">LEARN&nbsp;&nbsp;TO EARN</h1>
  <h2 class="course-title">BUSINESS ENRICHMENT COURSE</h2>
  <p class="tagline">A PROVEN SUCCESS OF HELPING PEOPLE IN THEIR LIVELIHOODS</p>
  <div class="skills-pill">BUSINESS SKILLS THAT<span class="accent">WILL HELP YOU</span></div>

  <div class="benefit-icon" style="left:49px">
    <svg viewBox="0 0 44 44" aria-hidden="true">
      <rect x="16" y="7" width="12" height="7" rx="2" fill="none" stroke="var(--orange)" stroke-width="3"/>
      <rect x="4" y="13" width="36" height="24" rx="4" fill="var(--orange)"/>
      <rect x="18" y="22" width="8" height="6" rx="1" fill="#ffffff"/>
    </svg>
  </div>
  <p class="benefit-label" style="left:161px">GET A<br>QUALITY JOB</p>

  <div class="benefit-icon" style="left:325px">
    <svg viewBox="0 0 44 44" aria-hidden="true">
      <rect x="5" y="28" width="6" height="12" fill="var(--orange)"/>
      <rect x="14" y="22" width="6" height="18" fill="var(--orange)"/>
      <rect x="23" y="26" width="6" height="14" fill="var(--orange)"/>
      <rect x="32" y="18" width="6" height="22" fill="var(--orange)"/>
      <polyline points="4,20 16,10 25,16 38,5" fill="none" stroke="var(--orange)" stroke-width="3"/>
      <polygon points="33,3 41,3 41,11" fill="var(--orange)"/>
    </svg>
  </div>
  <p class="benefit-label" style="left:438px">START/GROW<br>YOUR BUSINESS</p>

  <div class="benefit-icon" style="left:626px">
    <svg viewBox="0 0 44 44" aria-hidden="true">
      <polygon points="22,2 29,10 25,10 25,17 19,17 19,10 15,10" fill="var(--orange)"/>
      <rect x="4" y="20" width="36" height="20" rx="2" fill="none" stroke="var(--orange)" stroke-width="3"/>
      <circle cx="22" cy="30" r="4" fill="none" stroke="var(--orange)" stroke-width="2.5"/>
      <line x1="10" y1="30" x2="13" y2="30" stroke="var(--orange)" stroke-width="2.5"/>
      <line x1="31" y1="30" x2="34" y2="30" stroke="var(--orange)" stroke-width="2.5"/>
    </svg>
  </div>
  <p class="benefit-label" style="left:740px">INCREASE<br>YOUR SALARY</p>

  <div class="lesson-art" role="img" aria-label="Illustration of a smiling teacher in a blue suit and red tie pointing from an open laptop streaming a live lesson, with a stack of books and a pencil cup beside it"></div>

  <div class="topics">
    <p>• BUSINESS ADMIISTRATION &nbsp;• SMALL BUSINESS MANAGEMENT &nbsp;• FINANCE • &nbsp;INVESTMENTS • &nbsp;COMPUTERS</p>
    <p>• ACCOUNTING &nbsp;• SALES &nbsp;• MARKETING &nbsp;• PROJECT MANAGEMENT INTERVIEWING SKILLS • BUSINESS LAW</p>
    <p>• NEGOTIATION &nbsp;• PUBLIC SPEAKING &nbsp;• IMPORT/EXPORT • &nbsp;INFORMATION TECHNOLOY • DISTRIBUTION</p>
    <p>• MARKETING &nbsp;• LEDGERBOOKS &nbsp;• REAL ESTATE &nbsp;• HEALTH CARE • &nbsp;MANAGEMENT • &nbsp;MARKETSHOP</p>
  </div>
</main>
</body>
</html>
```